Verlindo Magician

I want the business card for my business to give to people who watch that later I will be employed to show magic here is my website http://www.verlindoillusions.example/I want the interesting design , i am very opened for formal and informal, I watch a lot of design so don't stick to the common shape and form but i hope it can also be produced the thing to write on will be the same as in picture that i will upload , i also will upload the logo for you that so can be easy to useDenis CostilleMagicianMAGICIAN VERLINDO 17 rue des Tilleuls - 25000 BESANÇON contact@verlindoillusions.example tel. 0381 946 157 tel. 0674 219 503

```html
<!DOCTYPE html>
<html lang="fr">
<head>
<meta charset="utf-8">
<title>Verlindo Magicien – Carte de visite</title>
<link rel="stylesheet" href="https://fonts.googleapis.com/css2?family=Questrial&display=swap">
<style>
  :root {
    --backdrop: #ececec;
    --card: #fbfbfb;
    --ink: #1a1a1a;
    --rule: #3a3a3a;
    --card-shadow: rgba(0, 0, 0, 0.12);
  }
  * { margin: 0; padding: 0; box-sizing: border-box; }
  html, body {
    width: 1200px;
    height: 800px;
    overflow: hidden;
    background: var(--backdrop);
  }
  body {
    font-family: "Questrial", "Century Gothic", sans-serif;
    color: var(--ink);
    position: relative;
  }
  .card {
    position: absolute;
    top: 231px;
    width: 520px;
    height: 338px;
    background: var(--card);
    box-shadow: 0 2px 10px var(--card-shadow);
  }
  .card--contact { left: 50px; }
  .card--brand { left: 630px; }

  /* Contact side */
  .identity {
    position: absolute;
    top: 78px;
    left: 30px;
    width: 196px;
    text-align: right;
  }
  .identity__name {
    font-size: 22px;
    letter-spacing: 0.2px;
    line-height: 1.1;
    text-transform: uppercase;
    white-space: nowrap;
  }
  .identity__role {
    font-size: 12px;
    letter-spacing: 0.6px;
    margin-top: 3px;
  }
  .identity__address {
    font-size: 14px;
    line-height: 1.35;
    margin-top: 4px;
  }
  .divider {
    position: absolute;
    top: 110px;
    left: 240px;
    width: 1.5px;
    height: 80px;
    background: var(--rule);
  }
  .contact-list {
    position: absolute;
    top: 120px;
    left: 254px;
    list-style: none;
    font-size: 13.5px;
    line-height: 1.45;
    white-space: nowrap;
  }

  /* Brand side */
  .brand {
    position: absolute;
    inset: 0;
    display: flex;
    flex-direction: column;
    align-items: center;
    justify-content: center;
    gap: 10px;
  }
  .brand__dot {
    width: 14px;
    height: 14px;
    border-radius: 50%;
    background: var(--ink);
  }
  .brand__name {
    font-size: 30px;
    letter-spacing: 3px;
    text-transform: uppercase;
  }
  .brand__role {
    font-size: 10px;
    letter-spacing: 2px;
    text-transform: uppercase;
    margin-top: -6px;
  }
</style>
</head>
<body>
  <section class="card card--contact">
    <div class="identity">
      <p class="identity__name">Marc Ravoulet</p>
      <p class="identity__role">MAGICIEN</p>
      <p class="identity__address">17 rue des Tilleuls<br>25000 BESANÇON</p>
    </div>
    <div class="divider"></div>
    <ul class="contact-list">
      <li>0381 946 157</li>
      <li>0674 219 503</li>
      <li>contact@verlindoillusions.example</li>
      <li>www.verlindoillusions.example</li>
    </ul>
  </section>

  <section class="card card--brand">
    <div class="brand">
      <span class="brand__dot"></span>
      <p class="brand__name">Verlindo</p>
      <p class="brand__role">Magicien</p>
    </div>
  </section>
</body>
</html>
```